Business Card for Industrial Distributor

We need a business card design for an industrial distributor. We sell machine parts for the manufacturing and oil industry. We would like the cards to look clean and modern but with a touch of industry.

Our colors are blue/white.

Please feel free to visit our website www.korvelpartsco.com

Target Market(s)

mexican manufacturers in the automobile/aerospace industry

Industry/Entity Type

Industrial

Colors
ffffff
0555a3

```html
<!DOCTYPE html>
<html lang="en">
<head>
<meta charset="utf-8">
<title>Korvel Business Card</title>
<link href="https://fonts.googleapis.com/css2?family=Open+Sans:wght@400;700;800&display=swap" rel="stylesheet">
<style>
  :root {
    --brand-navy: #283a8e;
    --brand-blue: #0555a3;
    --brand-glow: #1a78c2;
    --paper: #ffffff;
    --ink-grey: #5a5a66;
    --backdrop: #e9e6e1;
    --faint-mark: #eceef8;
  }
  * { margin: 0; padding: 0; box-sizing: border-box; }
  html, body { width: 1200px; height: 1076px; overflow: hidden; }
  body {
    background: var(--backdrop);
    font-family: "Open Sans", Verdana, sans-serif;
    position: relative;
  }
  .card {
    position: absolute;
    width: 751px;
    height: 432px;
    overflow: hidden;
    box-shadow: 0 6px 18px rgba(0,0,0,0.25);
  }
  /* Front side */
  .card--front {
    left: 110px;
    top: 80px;
    background: radial-gradient(ellipse at 50% 50%, var(--brand-glow) 0%, var(--brand-blue) 40%, var(--brand-navy) 100%);
    display: flex;
    align-items: center;
    justify-content: center;
  }
  .front-wordmark {
    color: var(--paper);
    font-weight: 800;
    font-size: 104px;
    letter-spacing: -1px;
  }
  /* Back side */
  .card--back {
    left: 298px;
    top: 543px;
    background: var(--paper);
  }
  .side-band {
    position: absolute;
    left: 0; top: 0;
    width: 87px; height: 100%;
    background: var(--brand-navy);
  }
  .faint-circle {
    position: absolute;
    left: 470px; top: 60px;
    width: 340px; height: 340px;
    border-radius: 50%;
    background: var(--faint-mark);
  }
  .brand {
    position: absolute;
    left: 105px; top: 46px;
    display: flex;
    align-items: center;
    gap: 18px;
  }
  .brand-dot {
    width: 98px; height: 98px;
    border-radius: 50%;
    background: var(--brand-blue);
  }
  .brand-name {
    color: var(--brand-navy);
    font-weight: 800;
    font-size: 90px;
    line-height: 1;
    letter-spacing: -1px;
  }
  .person {
    position: absolute;
    left: 105px; top: 232px;
  }
  .person-name {
    color: var(--brand-navy);
    font-weight: 800;
    font-size: 25px;
    line-height: 1;
  }
  .person-title {
    color: var(--ink-grey);
    font-size: 20px;
    line-height: 1.05;
  }
  .contact-list {
    position: absolute;
    left: 105px; top: 311px;
    list-style: none;
  }
  .contact-list li {
    display: flex;
    align-items: center;
    gap: 6px;
    height: 25px;
    color: var(--ink-grey);
    font-size: 19px;
  }
  .contact-icon { width: 20px; height: 20px; flex: none; }
  .web-highlight { color: var(--brand-navy); }
  .company {
    position: absolute;
    right: 33px; top: 330px;
    text-align: right;
  }
  .company-name {
    color: var(--brand-navy);
    font-weight: 700;
    font-size: 22px;
    line-height: 1.2;
  }
  .company-address {
    color: var(--ink-grey);
    font-size: 19px;
    line-height: 1.32;
  }
</style>
</head>
<body>

<section class="card card--front" aria-label="Card front">
  <span class="front-wordmark">Korvel</span>
</section>

<section class="card card--back" aria-label="Card back">
  <div class="side-band"></div>
  <div class="faint-circle"></div>

  <div class="brand">
    <div class="brand-dot"></div>
    <span class="brand-name">Korvel</span>
  </div>

  <div class="person">
    <p class="person-name">DANIEL REYES</p>
    <p class="person-title">Manager</p>
  </div>

  <ul class="contact-list">
    <li>
      <svg class="contact-icon" viewBox="0 0 20 20" aria-hidden="true"><rect width="20" height="20" fill="#283a8e"/><path d="M4 8 Q10 3 16 8 L14 10 L12 8 L8 8 L6 10 Z M5 11 H15 V15 H5 Z" fill="#fff"/></svg>
      <span>(555) 014 - 2290</span>
    </li>
    <li>
      <svg class="contact-icon" viewBox="0 0 20 20" aria-hidden="true"><rect width="20" height="20" fill="#283a8e"/><rect x="6" y="3" width="8" height="5" fill="#fff"/><rect x="3" y="8" width="14" height="6" fill="#fff"/><rect x="6" y="12" width="8" height="5" fill="#fff" stroke="#283a8e"/></svg>
      <span>(555) 014 - 2291</span>
    </li>
    <li>
      <svg class="contact-icon" viewBox="0 0 20 20" aria-hidden="true"><rect width="20" height="20" fill="#283a8e"/><rect x="3" y="5" width="14" height="10" fill="#fff"/><path d="M3 5 L10 11 L17 5 M3 15 L8 10 M17 15 L12 10" stroke="#283a8e" fill="none"/></svg>
      <span>sales@korvelpartsco.com</span>
    </li>
    <li>
      <svg class="contact-icon" viewBox="0 0 20 20" aria-hidden="true"><rect width="20" height="20" fill="#283a8e"/><circle cx="10" cy="10" r="6.5" fill="none" stroke="#fff" stroke-width="1.4"/><ellipse cx="10" cy="10" rx="2.8" ry="6.5" fill="none" stroke="#fff"/><path d="M3.5 10 H16.5" stroke="#fff"/></svg>
      <span>www.<span class="web-highlight">korvelparts</span>co.com</span>
    </li>
  </ul>

  <div class="company">
    <p class="company-name">Korvel International Corp.</p>
    <p class="company-address">4820 Harbor Line Rd.<br>Laredo, TX 78041</p>
  </div>
</section>

</body>
</html>
```